Elegant, High End Integrated Wellness Healthcare Practice

We need a brochure designed for an integrated mind-body wellness healthcare practice (www.quellarivecare.com) . This brochure will be used when we cold call prospects (physicians to refer to our office, and potential consumers to utilize our services). Our practice is geographically located in the middle Tennessee USA region, although we have plans to become an international company as many of our offerings can be accessed anywhere in the world. Ultimately our goal is to have this brochure used as a leave-behind in an effort to introduce our integrated offerings to increase market share. The final product brochure should be both elegant and serious, with clean lines but also convey warmth and trust, as individuals who are coming for our services have usually struggled with their health for a significant amount of time before finding our practice.
Updates

The design brief was very specific about providing a high-end science-based 2-page brochure (not flier). Several designs submitted were fliers. The other designs were heavy on yoga or "woo woo" non-science-based looking pictures. This is a flier to appeal to physicians and other healthcare providers. Therefore the design must speak science and evidence-based methods of mind and body wellness care. I would also like to appeal to the other designers I paid extra for their submissions and who have indicated they will "respond in the coming days."

```html
<!DOCTYPE html>
<html lang="en">
<head>
<meta charset="utf-8">
<title>Quellarive Care – Brochure</title>
<link href="https://fonts.googleapis.com/css2?family=Cinzel:wght@400;600&family=Poppins:wght@300;400;500;600;700&display=swap" rel="stylesheet">
<style>
:root{
  --green:#6aab45;
  --green-light:#8cc06a;
  --navy:#414c66;
  --navy-deep:#26314b;
  --orange:#e8894d;
  --paper:#f5f3ef;
  --ink:#4a4a4a;
  --stage:#3b3b3b;
  --white:#ffffff;
}
*{margin:0;padding:0;box-sizing:border-box}
html,body{width:768px;height:1200px;overflow:hidden}
body{background:var(--stage);font-family:"Poppins",sans-serif;color:var(--ink)}
.spread{position:absolute;left:16px;width:736px;height:540px;display:flex;box-shadow:0 10px 30px rgba(0,0,0,.35)}
.spread--outer{top:40px}
.spread--inner{top:620px}
.page{position:relative;width:368px;height:540px;overflow:hidden;background:var(--paper)}
.abs{position:absolute}
.serif{font-family:"Cinzel",serif}

/* back cover */
.back-photo{left:0;top:0;width:368px;height:340px;background:radial-gradient(circle at 30% 40%,#ffffff 0%,#efe9e0 45%,#ddd5c8 100%)}
.back-copy{left:28px;top:30px;width:312px;font-size:8.4px;line-height:1.55;color:#5a5a5a}
.back-copy p{margin-bottom:9px}
.back-shape{left:0;top:0}
.back-contact{left:28px;top:378px;width:316px;color:var(--white)}
.back-contact .name{font-size:21px;letter-spacing:.5px}
.back-contact .addr{font-size:9.5px;margin:6px 0 10px}
.phone-pill{display:inline-block;background:var(--green);border-radius:20px;padding:6px 12px;font-size:8.2px;font-weight:600;white-space:nowrap}
.back-contact .hours{font-size:9px;margin-top:10px}
.back-contact .hours b{font-weight:600}
.back-contact .url{font-size:10.5px;letter-spacing:1.5px;margin-top:10px}

/* front cover */
.brand{right:26px;top:40px;display:flex;align-items:center;gap:8px}
.brand-dot{width:30px;height:30px;border-radius:50%;background:var(--green)}
.brand-name{font-family:"Cinzel",serif;font-size:18px;color:#3d4a35;line-height:1.1}
.front-photo{left:0;top:0;width:368px;height:540px;background:linear-gradient(160deg,#c9c4ae 0%,#8e8f6d 40%,#6a5a6e 70%,#8b3d5c 100%);clip-path:polygon(14% 27%,100% 19%,100% 82%,0 82%,0 30%)}
.front-shape{left:0;top:0}
.welcome{left:0;top:408px;width:368px;text-align:center;color:var(--white)}
.welcome h1{font-family:"Cinzel",serif;font-weight:600;font-size:19px;line-height:1.15}
.welcome .sub{font-family:"Cinzel",serif;font-size:9.5px;margin-top:6px;line-height:1.35}
.url-pill{display:inline-block;border:1px solid rgba(255,255,255,.8);border-radius:20px;padding:5px 18px;font-size:10px;letter-spacing:1.5px;margin-top:10px}
.url-pill b{font-weight:700}

/* inner left */
.inner-bg{left:0;top:0;width:368px;height:540px;background:linear-gradient(180deg,var(--paper) 0%,#eceff3 55%,#e3e8ef 70%,var(--paper) 85%)}
.services{left:24px;top:66px;width:170px}
.heading-light{color:var(--green);font-size:14px;font-weight:300;letter-spacing:1px}
.heading-block{display:inline-block;background:var(--navy);color:var(--white);font-weight:700;font-size:14px;letter-spacing:1px;padding:1px 10px 2px 6px}
.heading-block .heading-light{font-size:13px}
.tick-list{list-style:none;margin-top:6px}
.tick-list li{display:flex;align-items:center;gap:6px;font-size:9.5px;font-weight:500;color:#3c3c3c;margin-bottom:4px}
.tick-list svg{flex:none}
.other{margin-top:12px}
.package{left:196px;top:40px;width:150px;height:276px;background:var(--green-light);padding:22px 16px;color:var(--white)}
.package h2{font-size:17px;line-height:1.05;font-weight:300;letter-spacing:.5px}
.package h2 b{font-weight:700}
.package hr{border:0;border-top:1px solid rgba(255,255,255,.7);margin:14px 0}
.package p{font-size:9px;line-height:1.5}
.fold{right:0;bottom:0}
.practice-copy{left:24px;top:350px;width:320px;font-size:8.6px;line-height:1.55;color:#3e3e3e}
.tagline{color:var(--green);font-weight:600;font-size:9px;margin-top:6px}
.footer{left:0;bottom:0;width:368px;height:40px;background:var(--navy-deep);border-top:3px solid var(--green);color:var(--white);font-size:10px;letter-spacing:1.5px;text-align:center;line-height:37px}

/* inner right */
.couple-photo{left:0;top:0;width:368px;height:300px;background:linear-gradient(180deg,#e9edf3 0%,#d5dde8 55%,#9aa9c1 80%,#7c8ca8 100%)}
.approach{left:22px;top:40px;width:178px}
.approach-label{display:inline-block;background:var(--navy);color:var(--white);font-size:9px;font-weight:700;letter-spacing:.5px;padding:3px 10px}
.approach p{font-size:8.4px;line-height:1.55;color:#3c3c3c;margin-top:8px}
.approach .tagline{font-size:8.4px;color:#555}
.reviews{left:22px;top:318px;width:324px}
.reviews h2{font-size:12px;font-weight:400;color:var(--navy-deep);letter-spacing:.3px;padding-bottom:6px;border-bottom:1px solid #b9bcc2}
.reviews h2 b{font-weight:700}
.review-cols{display:flex;gap:16px;margin-top:10px}
.review{position:relative;font-size:7.8px;line-height:1.5;color:#4a4a4a;padding-left:12px}
.review--short{width:100px}
.review--long{flex:1}
.review .mark{position:absolute;left:0;top:-6px;font-size:26px;color:#cfd3d8;font-family:Georgia,serif}
.review .who{color:var(--green);font-weight:700;margin-top:4px}
</style>
</head>
<body>

<section class="spread spread--outer">
  <article class="page page--back">
    <div class="abs back-photo" role="img" aria-label="Soft warm bokeh background photo"></div>
    <div class="abs back-copy">
      <p>At Quellarive Care we facilitate body and mind health and wellness through an integrated functional approach to care. This method of personalized care appreciates you as a unique individual with distinct health circumstances. We tailor our body and mind approaches to address your specific health concerns. Through the combination of body and mind interventions, we address concerns such as Attention Deficit, Distractibility and learning concerns, chronic pain and inflammation conditions, and mind health conditions such as anxiety, depression, panic, and many more.</p>
      <p>The result is integrative healing-oriented care that addresses aspects of your whole person (body, mind, and spirit). Book a 10 minute consultation to find out how a body and mind consultation can help you live your best life in optimal wellness, call us today or book a consultation online. Please note, this is only for consultation calls regarding our package for a HEALTHY LIFESTYLE FOR LIFE.</p>
      <p>We are conveniently located at 418 Linden Hollow Rd. Elmford, TN 37990. We serve clients in Elmford, Ashby Falls, Corran Ridge, Wexley, Dunmore Glen, Halvet, and surrounding areas.</p>
    </div>
    <svg class="abs back-shape" width="368" height="540" viewBox="0 0 368 540" aria-hidden="true">
      <polygon points="40,330 100,300 170,370" fill="#6aab45"/>
      <path d="M0 370 C90 330 230 320 368 350 L368 540 L0 540 Z" fill="#414c66"/>
    </svg>
    <div class="abs back-contact">
      <div class="name serif">Quellarive Care</div>
      <div class="addr">418 Linden Hollow Rd. Elmford, TN 37990</div>
      <div class="phone-pill">New Patients: (555) 014 2280 / Existing Patients: (555) 014 3391</div>
      <div class="hours"><b>OPERATING HOURS :</b> Monday - Friday: 8am - 7pm</div>
      <div class="url">www.quellarivecare.com</div>
    </div>
  </article>

  <article class="page page--front">
    <div class="abs front-photo" role="img" aria-label="Photo of a hiker in a beanie breathing calmly outdoors"></div>
    <div class="abs brand">
      <span class="brand-dot"></span>
      <span class="brand-name">Quellarive<br>Care</span>
    </div>
    <svg class="abs front-shape" width="368" height="540" viewBox="0 0 368 540" aria-hidden="true">
      <path d="M0 385 C120 395 250 420 368 440 L368 540 L0 540 Z" fill="#6aab45"/>
      <polygon points="268,400 296,372 300,400" fill="#e8894d"/>
      <polygon points="266,402 322,402 292,446" fill="#ffffff"/>
      <line x1="30" y1="500" x2="90" y2="500" stroke="#fff" stroke-width="1"/>
      <line x1="278" y1="500" x2="338" y2="500" stroke="#fff" stroke-width="1"/>
    </svg>
    <div class="abs welcome">
      <h1>Welcome to<br>Quellarive Care,</h1>
      <div class="sub">Integrated Body and Mind Health,<br>Wellness Center Located in Elmford, TN</div>
      <div class="url-pill">www.<b>QuellariveCare</b>.com</div>
    </div>
  </article>
</section>

<section class="spread spread--inner">
  <article class="page page--services">
    <div class="abs inner-bg" role="img" aria-label="Faint misty mountain landscape background"></div>
    <div class="abs services">
      <div class="heading-light">FEATURED</div>
      <div class="heading-block">SERVICES</div>
      <ul class="tick-list">
        <li><svg width="9" height="9" viewBox="0 0 10 10"><circle cx="5" cy="5" r="4.3" fill="none" stroke="#6aab45"/><path d="M3 5.2l1.4 1.4L7.2 3.8" fill="none" stroke="#6aab45" stroke-width="1.2"/></svg>Tonal Brain Care</li>
        <li><svg width="9" height="9" viewBox="0 0 10 10"><circle cx="5" cy="5" r="4.3" fill="none" stroke="#6aab45"/><path d="M3 5.2l1.4 1.4L7.2 3.8" fill="none" stroke="#6aab45" stroke-width="1.2"/></svg>Functional Medicine</li>
        <li><svg width="9" height="9" viewBox="0 0 10 10"><circle cx="5" cy="5" r="4.3" fill="none" stroke="#6aab45"/><path d="M3 5.2l1.4 1.4L7.2 3.8" fill="none" stroke="#6aab45" stroke-width="1.2"/></svg>Healthy Lifestyle For Life</li>
        <li><svg width="9" height="9" viewBox="0 0 10 10"><circle cx="5" cy="5" r="4.3" fill="none" stroke="#6aab45"/><path d="M3 5.2l1.4 1.4L7.2 3.8" fill="none" stroke="#6aab45" stroke-width="1.2"/></svg>Lumapulse For Pain</li>
      </ul>
      <div class="other">
        <div class="heading-block"><span class="heading-light">OTHER</span> SERVICES</div>
        <ul class="tick-list">
          <li><svg width="9" height="9" viewBox="0 0 10 10"><circle cx="5" cy="5" r="4.3" fill="none" stroke="#6aab45"/><path d="M3 5.2l1.4 1.4L7.2 3.8" fill="none" stroke="#6aab45" stroke-width="1.2"/></svg>Whole Body Wellness</li>
          <li><svg width="9" height="9" viewBox="0 0 10 10"><circle cx="5" cy="5" r="4.3" fill="none" stroke="#6aab45"/><path d="M3 5.2l1.4 1.4L7.2 3.8" fill="none" stroke="#6aab45" stroke-width="1.2"/></svg>Brain Wave Mapping</li>
          <li><svg width="9" height="9" viewBox="0 0 10 10"><circle cx="5" cy="5" r="4.3" fill="none" stroke="#6aab45"/><path d="M3 5.2l1.4 1.4L7.2 3.8" fill="none" stroke="#6aab45" stroke-width="1.2"/></svg>Wellness Package</li>
          <li><svg width="9" height="9" viewBox="0 0 10 10"><circle cx="5" cy="5" r="4.3" fill="none" stroke="#6aab45"/><path d="M3 5.2l1.4 1.4L7.2 3.8" fill="none" stroke="#6aab45" stroke-width="1.2"/></svg>Nutritional Wellness</li>
        </ul>
      </div>
    </div>
    <div class="abs package">
      <h2>WELLNESS<br><b>PACKAGE</b></h2>
      <hr>
      <p>We offer a unique wellness package you won't find anywhere else, a combination of a body and mind system designed to "Reunite" your brain and your gut!</p>
      <svg class="abs fold" width="34" height="34" viewBox="0 0 34 34" aria-hidden="true">
        <polygon points="34,0 0,34 34,34" fill="#f5f3ef"/>
        <polygon points="34,0 0,34 6,6" fill="#4f8a33"/>
      </svg>
    </div>
    <div class="abs practice-copy">
      <p>The practitioners at Quellarive Care have significant experience working with whole-body approaches to care. Whole body health requires that the body and mind are aligned. Although pharmaceuticals and "talk therapy" can be beneficial we have found that these methods often fall short to address concerns that brought the individual to our office. Body changes are often missing. When one's body changes the mind can more readily integrate other parts of a person's approach to life. The result is integrative healing-oriented care that addresses aspects of the whole person (body, mind, and spirit).</p>
      <p class="tagline">Find a clearer path to a fuller you</p>
    </div>
    <div class="abs footer">www.quellarivecare.com</div>
  </article>

  <article class="page page--approach">
    <div class="abs couple-photo" role="img" aria-label="Photo of two people on a mountain top raising joined hands"></div>
    <div class="abs approach">
      <span class="approach-label">OUR UNIQUE APPROACH</span>
      <p>At Quellarive Care we facilitate body and mind health and wellness through an integrated functional approach to care. This method of personalized care appreciates you as a unique individual with distinct health circumstances. We tailor our body and mind approaches to address your specific health concerns. The result is integrative healing-oriented care that addresses aspects of your whole person (body, mind, and spirit).</p>
      <p class="tagline">Find a clearer path to a fuller you</p>
    </div>
    <div class="abs reviews">
      <h2>PATIENT REVIEWS <b>AND FEEDBACK</b></h2>
      <div class="review-cols">
        <div class="review review--short">
          <span class="mark">“</span>
          Dr. Halloran is amazing at giving advice on how to handle different situations. Amazing listener and very good at explaining how to figure out certain behaviors or feelings one may be experiencing.
          <div class="who">KT</div>
        </div>
        <div class="review review--long">
          <span class="mark">“</span>
          I have been seeing Dr. Halloran for some time now and cannot say enough about how grateful I am to have found her! She is professional and easy to talk to. She has established a warm and welcoming environment where you feel comfortable speaking freely. Dr. Halloran is straightforward, which I LOVE! The receptionist is the sweetest! They are very accommodating and offer zoom sessions as well as in person. My daughter sees Dr. Pruett which we have been happy with as well. I highly recommend this team!
          <div class="who">Ana M.</div>
        </div>
      </div>
    </div>
    <div class="abs footer">www.quellarivecare.com</div>
  </article>
</section>

</body>
</html>
```